update of B2B website and conversion to single page

The current website needs to be modernized. I want what is commonly called a single page website. It is not actually a single page. See some examples here:
https://www.plivenor.example/
https://www.quorbel.example/
https://www.trindavex.example/
Most or all graphics will be replaced.
Please see the attached spreadsheet for a rough draft of the home page layout. Convert the existing website at https://www.zolvarin.example/ to a single page website. We will provide the page content. You will provide all of the design, graphics, development, production deployment. etc. The look and feel should be corporate, polished, premium.

```html
<!DOCTYPE html>
<html lang="en">
<head>
<meta charset="utf-8">
<title>Zolvarin – Enterprise Data Quality Made Easy</title>
<link rel="stylesheet" href="https://fonts.googleapis.com/css2?family=Lato:wght@400;700;900&family=Montserrat:wght@400;500;700&display=swap">
<style>
:root{
  --navy:#2b3180;
  --hero:#333f8b;
  --gold:#f9b90f;
  --footer:#232a5b;
  --grey:#efefef;
  --ink:#222;
  --white:#fff;
}
*{box-sizing:border-box;margin:0;padding:0}
html,body{width:718px;height:1200px;overflow:hidden;background:var(--white)}
body{position:relative;font-family:'Lato',sans-serif;color:var(--ink)}
.abs{position:absolute}

/* top bar */
.topbar{left:0;top:0;width:718px;height:45px;background:#f6f6f6}
.social{left:80px;top:6px;display:flex;gap:6px}
.social span{width:11px;height:11px;background:var(--gold);transform:rotate(45deg);display:block}
.contact{right:80px;top:8px;font-size:8px;color:#333;display:flex;gap:12px;align-items:center;white-space:nowrap}
.contact svg{vertical-align:-1px;margin-right:4px}

/* hero */
.hero{left:0;top:45px;width:718px;height:236px;background:var(--hero);overflow:hidden}
.nav{left:79px;top:26px;width:561px;height:38px;background:var(--white);box-shadow:0 2px 6px rgba(0,0,0,.25);z-index:2}
.brand{left:14px;top:10px;font-weight:900;font-size:17px;color:var(--navy);display:flex;align-items:center;gap:6px}
.brand i{width:10px;height:10px;background:var(--gold);display:block}
.menu{right:14px;top:15px;display:flex;gap:13px;font-family:'Montserrat',sans-serif;font-size:6.8px;color:#333;font-weight:500;white-space:nowrap}
.hero-kicker{left:79px;top:70px;font-family:'Montserrat',sans-serif;font-size:10.5px;letter-spacing:1.4px;color:var(--white);white-space:nowrap}
.hero-title{left:78px;top:92px;font-family:'Montserrat',sans-serif;font-size:17px;letter-spacing:1.8px;color:var(--white);font-weight:500;white-space:nowrap}
.btn-signup{left:79px;top:135px;width:82px;height:24px;background:var(--white);color:#2a5d8f;font-size:7.5px;font-weight:900;display:flex;align-items:center;justify-content:center;letter-spacing:.3px}
.hero-art{left:432px;top:22px;width:216px;height:200px;border-radius:8px;background:linear-gradient(160deg,#e9ecf6 0%,#8f97c5 45%,#3f4756 100%);opacity:.85}

/* intro */
.intro-title{left:0;top:315px;width:718px;text-align:center;font-family:'Montserrat',sans-serif;font-size:12px;font-weight:400;letter-spacing:1.3px;color:var(--navy)}
.intro-title b{color:var(--gold);font-weight:400}
.intro-rule{left:358px;top:340px;width:28px;height:3px;border-top:1px solid #5ab0c8;border-bottom:1px solid #5ab0c8}
.intro-text{left:140px;top:357px;width:438px;text-align:center;font-size:8px;line-height:14px;color:#222}
.card{top:416px;width:132px}
.card-head{display:flex;align-items:center;gap:6px;height:34px}
.card-icon{width:33px;height:33px;border-radius:50%;border:1px solid #ccc;display:flex;align-items:center;justify-content:center;flex:none}
.card-name{font-size:8.6px;color:var(--navy);font-weight:400;white-space:nowrap}
.card-text{margin-top:10px;font-size:6.5px;line-height:10.4px;color:#222;height:31px;overflow:hidden}
.card-more{margin-top:4px;font-size:5.5px;color:var(--gold);font-weight:700}

/* services band */
.band{left:0;top:528px;width:718px;height:380px}
.services-art{left:84px;top:614px;width:228px;height:228px;border-radius:50%;background:radial-gradient(circle at 45% 45%,#3a2da0 0%,#24167a 60%,#1b1060 100%)}
.services-shadow{left:100px;top:836px;width:200px;height:10px;border-radius:50%;background:radial-gradient(ellipse,rgba(0,0,0,.35),rgba(0,0,0,0) 70%)}
.services-title{left:348px;top:611px;font-size:19px;font-weight:900;color:var(--navy);letter-spacing:-.2px;white-space:nowrap}
.services-title span{color:var(--gold)}
.services-rule{left:348px;top:635px;width:30px;height:2px;background:var(--gold)}
.services-text{left:348px;top:651px;width:265px;font-size:7.2px;line-height:11px;color:#222}
.services-list{left:348px;top:697px;list-style:none;font-size:7.4px;color:#111}
.services-list li{height:18px;display:flex;align-items:center;gap:6px;white-space:nowrap}
.services-list li::before{content:"";width:2.5px;height:2.5px;background:var(--navy);border-radius:50%}
.btn-trial-dark{left:349px;top:794px;width:82px;height:24px;background:var(--navy);color:var(--gold);font-size:8px;font-weight:900;display:flex;align-items:center;justify-content:center}

/* offer */
.offer-title{left:0;top:915px;width:718px;text-align:center;font-size:17px;font-weight:900;color:var(--navy)}
.offer-text{left:0;top:943px;width:718px;text-align:center;font-size:8.6px;color:#222}
.btn-trial-gold{left:321px;top:970px;width:81px;height:23px;background:var(--gold);color:var(--navy);font-size:8px;font-weight:900;display:flex;align-items:center;justify-content:center}

/* footer */
.footer{left:0;top:1028px;width:718px;height:172px;background:var(--footer)}
.footer-brand{left:66px;top:1056px;font-weight:900;font-size:17px;color:var(--white);display:flex;align-items:center;gap:6px}
.footer-brand i{width:10px;height:10px;background:var(--gold);display:block}
.footer-col{top:1057px}
.footer-col h4{font-size:8.6px;font-weight:700;color:var(--gold);margin-bottom:9px;white-space:nowrap}
.footer-col li{list-style:none;font-family:'Montserrat',sans-serif;font-size:6.5px;color:#e5e7f3;height:13.5px;white-space:nowrap}
.footer-rule{left:0;top:1176px;width:718px;height:1px;background:#3a4280}
.copyright{left:0;top:1184px;width:718px;text-align:center;font-family:'Montserrat',sans-serif;font-size:6.5px;color:#e5e7f3}
</style>
</head>
<body>

<div class="abs topbar"></div>
<div class="abs social" aria-label="Social links"><span></span><span></span><span></span><span></span></div>
<div class="abs contact">
  <span><svg width="8" height="8" viewBox="0 0 24 24"><path fill="#333" d="M6.6 10.8a15 15 0 0 0 6.6 6.6l2.2-2.2c.3-.3.7-.4 1-.2 1.1.4 2.3.6 3.6.6.6 0 1 .4 1 1V20c0 .6-.4 1-1 1A17 17 0 0 1 3 4c0-.6.4-1 1-1h3.5c.6 0 1 .4 1 1 0 1.3.2 2.5.6 3.6.1.3 0 .7-.2 1z"/></svg>(555) 014-2280</span>
  <span><svg width="8" height="7" viewBox="0 0 24 20"><path fill="#333" d="M0 0h24v20H0z"/><path fill="#f6f6f6" d="M2 2l10 8 10-8v2l-10 8L2 4z"/></svg>info@zolvarin.example</span>
</div>

<section class="abs hero">
  <div class="abs hero-art" role="img" aria-label="Illustration of cloud icons above a stack of database servers"></div>
  <p class="abs hero-kicker">Data Concept • Data Cleansing • Tabulix</p>
  <h1 class="abs hero-title">Data Quality Proof of Concept</h1>
  <a class="abs btn-signup">SIGN UP NOW!</a>
</section>

<nav class="abs nav">
  <div class="abs brand"><i></i>Zolvarin</div>
  <div class="abs menu">
    <span>SERVICES</span><span>CONNECTORS ▾</span><span>FEATURES ▾</span><span>WHY ZV*PLUS? ▾</span><span>OFFERS ▾</span><span>BLOG</span><span>COMPANY</span>
  </div>
</nav>

<h2 class="abs intro-title">ENTERPRISE <b>DATA QUALITY</b> MADE EASY</h2>
<div class="abs intro-rule"></div>
<p class="abs intro-text">Cleanse data, verify addresses, find and consolidate duplicate records in batch and real time. Connectors for Orvanta E-Business Suite, Cloudmarta and Selbrin applications and Kestrel DB, Norvik SQL Server and Orvanta databases.</p>

<div class="abs card" style="left:92px">
  <div class="card-head"><div class="card-icon"><svg width="16" height="14" viewBox="0 0 24 20" fill="none" stroke="#555" stroke-width="1.3"><path d="M6 16a5 5 0 0 1 0-10 6 6 0 0 1 11 1 4 4 0 0 1 1 8"/><rect x="8" y="10" width="8" height="8"/></svg></div><span class="card-name">Zolvarin</span></div>
  <p class="card-text">The ZV*Plus Kestrel DB Database Connector eliminates the need for custom integration work, saving</p>
  <p class="card-more">Read More ..</p>
</div>
<div class="abs card" style="left:236px">
  <div class="card-head"><div class="card-icon"><svg width="14" height="16" viewBox="0 0 20 24" fill="none" stroke="#555" stroke-width="1.3"><rect x="2" y="3" width="14" height="19"/><path d="M6 13l3 3 8-9"/></svg></div><span class="card-name">Data Quality</span></div>
  <p class="card-text">ZV*Plus Batch works in the background, cleansing data, and identifying and merging duplicates accord-</p>
  <p class="card-more">Read More ..</p>
</div>
<div class="abs card" style="left:382px">
  <div class="card-head"><div class="card-icon"><svg width="14" height="16" viewBox="0 0 20 24" fill="none" stroke="#555" stroke-width="1.3"><ellipse cx="10" cy="4" rx="8" ry="3"/><path d="M2 4v16c0 1.7 3.6 3 8 3s8-1.3 8-3V4M2 10c0 1.7 3.6 3 8 3s8-1.3 8-3M2 15c0 1.7 3.6 3 8 3s8-1.3 8-3"/></svg></div><span class="card-name">Selbrin Connector</span></div>
  <p class="card-text">The ZV*Plus Selbrin Connector eliminates integration work, saving your business time and money.</p>
  <p class="card-more">Read More ..</p>
</div>
<div class="abs card" style="left:523px">
  <div class="card-head"><div class="card-icon"><svg width="16" height="16" viewBox="0 0 24 24" fill="none" stroke="#333" stroke-width="1.8"><path d="M4 12a8 8 0 0 1 14-5M20 12a8 8 0 0 1-14 5"/><path d="M18 3v4h-4M6 21v-4h4"/><circle cx="12" cy="12" r="2.5"/></svg></div><span class="card-name">Web Service APIs</span></div>
  <p class="card-text">ZV*Plus Web Service APIs enable you to embed data quality processes anywhere in your enterprise including</p>
  <p class="card-more">Read More ..</p>
</div>

<svg class="abs band" viewBox="0 0 718 380" aria-hidden="true"><polygon points="0,72 718,0 718,308 0,380" fill="var(--grey)"/></svg>
<div class="abs services-art" role="img" aria-label="Illustration of a server rack connected to a laptop on a circuit board"></div>
<div class="abs services-shadow"></div>
<h2 class="abs services-title"><span>PROFESSIONAL</span> SERVICES</h2>
<div class="abs services-rule"></div>
<p class="abs services-text">Zolvarin consultants are Customer Data experts. We provide high value services to solve your biggest data challenges. Zolvarin has staffed and managed several large scale data projects including:</p>
<ul class="abs services-list">
  <li>Data Quality</li>
  <li>Customer Master / Master Data Management</li>
  <li>Data Governance</li>
  <li>Data Integration</li>
  <li>Data Migration</li>
</ul>
<a class="abs btn-trial-dark">FREE TRAIL</a>

<h2 class="abs offer-title">WHAT WE OFFER?</h2>
<p class="abs offer-text">This Free Trial includes the cleansing of 10,000 address records.</p>
<a class="abs btn-trial-gold">FREE TRAIL</a>

<footer class="abs footer"></footer>
<div class="abs footer-brand"><i></i>Zolvarin</div>
<div class="abs footer-col" style="left:234px">
  <h4>QUICK MENU</h4>
  <ul><li>Services</li><li>Connectors</li><li>Features</li><li>FAQs</li><li>Offers</li><li>Company</li></ul>
</div>
<div class="abs footer-col" style="left:363px">
  <h4>FEATURE</h4>
  <ul><li>Address Verification &amp; Data Cleansing</li><li>Data Enrichment</li><li>Duplicate Record Match &amp; Merge</li><li>Batch and Persistent &amp; Quality</li><li>Real Time Interactive Data Quality</li><li>Data Quality Anywhere – Web Service</li></ul>
</div>
<div class="abs footer-col" style="left:533px">
  <h4>LEGAL INFOMATION</h4>
  <ul><li>Blog</li><li>Term &amp; Condiditon</li><li>Privacy Policty</li></ul>
</div>
<div class="abs footer-rule"></div>
<p class="abs copyright">Copyright © 2018 Zolvarin. All rights Reserved</p>

</body>
</html>
```